Business Card Design For Marketing Agnecy LVP

Need business card design for marketing agency.

Doug Fenwick
President, CEO
1-555-302-4196
doug@boldpromoperksgroup.example
www.BoldPromoPerksGroup.example

Back Side:
Boost Sales Using Rewards, Incentives & Giveaways
Get A Free Sample Package

Target Market(s)

B2B

Industry/Entity Type

Marketing

Contact Information for Business Card

Doug Fenwick
President, CEO
1-555-302-4196

Back Side:
Get A Free Sample Package

Please note that my current url is OLD DESIGN. I am working on new design and want the business card to match color themes at least on new site. Here is the demo link for new site so you can see the colors I use, etc.

http://layoutcratehub.example/kq/doug/lvp_final/index.html

Requirements
Must have
• Please note that my current url is OLD DESIGN. I am working on new design and want the business card to match color themes at least on new site. Here is the demo link for new site so you can see the colors I use, etc.

Nice to have

Should not have

```html
<!DOCTYPE html>
<html lang="en">
<head>
<meta charset="utf-8">
<title>LVP Business Card</title>
<link href="https://fonts.googleapis.com/css2?family=Montserrat:wght@400;500;600;700&display=swap" rel="stylesheet">
<style>
  :root {
    --brand-blue: #1f74c1;
    --brand-grey: #55585c;
    --paper: #ffffff;
    --canvas-bg: #e9ebee;
    --text-light: #ffffff;
  }
  * { box-sizing: border-box; margin: 0; padding: 0; }
  html, body {
    width: 1200px; height: 1015px; overflow: hidden;
    background: var(--canvas-bg);
    font-family: "Montserrat", Arial, sans-serif;
  }
  .sheet {
    width: 1200px; height: 1015px;
    display: flex; flex-direction: column; align-items: center; justify-content: center;
    gap: 36px;
  }
  .card {
    position: relative; width: 800px; height: 457px; overflow: hidden;
    box-shadow: 0 10px 26px rgba(0,0,0,0.18);
  }
  /* Back side */
  .card-back {
    background: var(--brand-blue);
    color: var(--text-light);
    display: flex; flex-direction: column; align-items: center; justify-content: center;
    text-align: center;
  }
  .back-pitch {
    font-weight: 600; font-size: 29px; line-height: 1.55; letter-spacing: 0.5px;
    text-transform: uppercase;
  }
  .back-rule {
    width: 470px; height: 1px; background: rgba(255,255,255,0.55);
    margin: 34px 0 26px;
  }
  .back-url { font-size: 27px; font-weight: 500; letter-spacing: 0.3px; }

  /* Front side */
  .card-front { background: var(--paper); }
  .front-wave { position: absolute; inset: 0; }
  .brand-name {
    position: absolute; left: 64px; top: 140px;
    color: var(--brand-blue); font-weight: 700;
    display: flex; flex-direction: column; align-items: flex-start;
  }
  .brand-initials {
    font-size: 96px; line-height: 1; letter-spacing: 2px;
    display: flex; align-items: center; gap: 12px;
  }
  .brand-dot { width: 20px; height: 20px; border-radius: 50%; background: var(--brand-blue); }
  .brand-full { font-size: 25px; line-height: 1.15; margin-top: 8px; text-transform: uppercase; }
  .contact {
    position: absolute; right: 46px; top: 200px;
    color: var(--text-light); text-align: right;
  }
  .contact-name { font-size: 25px; font-weight: 700; text-transform: uppercase; letter-spacing: 0.3px; }
  .contact-title { font-size: 17px; font-weight: 400; margin-top: 2px; }
  .contact-lines { margin-top: 44px; font-size: 16px; line-height: 1.45; }
  .contact-line { display: flex; align-items: center; justify-content: flex-end; gap: 8px; }
  .contact-line svg { width: 15px; height: 15px; flex: none; }
</style>
</head>
<body>
<main class="sheet">
  <section class="card card-back" aria-label="Card back">
    <p class="back-pitch">Boost sales using rewards<br>incentives &amp; giveaways<br>Get a free sample package</p>
    <div class="back-rule"></div>
    <p class="back-url">www.BoldPromoPerksGroup.example</p>
  </section>

  <section class="card card-front" aria-label="Card front">
    <svg class="front-wave" viewBox="0 0 800 457" aria-hidden="true">
      <path d="M800 80 C620 60 500 100 440 210 C390 300 310 390 150 457 L800 457 Z" fill="var(--brand-blue)"/>
      <path d="M800 80 C620 60 500 100 440 210 C390 300 310 390 150 457" transform="translate(-14,-30)" fill="none" stroke="var(--brand-grey)" stroke-width="8"/>
      <path d="M800 80 C620 60 500 100 440 210 C390 300 310 390 150 457" transform="translate(-7,-15)" fill="none" stroke="var(--brand-blue)" stroke-width="3"/>
    </svg>

    <div class="brand-name">
      <div class="brand-initials">LVP <span class="brand-dot"></span></div>
      <div class="brand-full">Bold Promo<br>Perks Group</div>
    </div>

    <div class="contact">
      <p class="contact-name">Doug Fenwick</p>
      <p class="contact-title">President, CEO</p>
      <div class="contact-lines">
        <p class="contact-line">1-555-302-4196
          <svg viewBox="0 0 16 16"><path d="M3 1.5h3l1.2 3.3-1.8 1.2a8 8 0 0 0 4.6 4.6l1.2-1.8 3.3 1.2v3c0 .6-.5 1-1 1A13 13 0 0 1 2 2.5c0-.5.4-1 1-1z" fill="#fff"/></svg></p>
        <p class="contact-line">doug@boldpromoperksgroup.example
          <svg viewBox="0 0 16 16"><rect x="1" y="3" width="14" height="10" rx="1" fill="#fff"/><path d="M1.5 3.5 8 9l6.5-5.5" fill="none" stroke="var(--brand-blue)" stroke-width="1.4"/></svg></p>
        <p class="contact-line">www.BoldPromoPerksGroup.example
          <svg viewBox="0 0 16 16"><circle cx="8" cy="8" r="7" fill="#fff"/><path d="M1 8h14M8 1c-3 3.5-3 10.5 0 14M8 1c3 3.5 3 10.5 0 14" fill="none" stroke="var(--brand-blue)" stroke-width="1"/></svg></p>
      </div>
    </div>
  </section>
</main>
</body>
</html>
```